corvale institute of business and technology web site

I need web site for the institute which focus on business courses and computer course it is also for vocation train for employment It is also carear development and advancement .It should have links to online study resource which free
Industry/Entity Type
Business
Number of Pages Required
1 page
Look and feel
Each slider illustrates characteristics of the customer's brand and the style your logo design should communicate.

```html
<!DOCTYPE html>
<html lang="en">
<head>
<meta charset="utf-8">
<title>Corvale Institute of Business and Technology</title>
<link href="https://fonts.googleapis.com/css2?family=Open+Sans:wght@400;600;700;800&family=Oswald:wght@400;500&display=swap" rel="stylesheet">
<style>
:root{
  --blue:#1b7fd3;
  --blue-dark:#0f5a9e;
  --sky:#4aa9ea;
  --sky-pale:#cfe7f8;
  --orange:#f7941d;
  --grey-bg:#eceef0;
  --text:#555b61;
  --footer:#3c4147;
  --footer-dark:#31353a;
  --white:#fff;
}
*{box-sizing:border-box;margin:0;padding:0}
html,body{width:1200px;height:2944px;overflow:hidden}
body{font-family:"Open Sans",Arial,sans-serif;color:var(--text);background:var(--footer-dark);font-size:14px;line-height:1.5}
.page{background:var(--white)}
.wrap{width:1080px;margin:0 auto;position:relative}
a{color:inherit;text-decoration:none}

/* header */
.site-header{height:180px;background:linear-gradient(180deg,var(--blue) 0%,var(--sky) 100%);color:var(--white);position:relative}
.topbar{display:flex;gap:26px;font-size:13px;padding-top:6px;height:34px;align-items:center}
.topbar span{display:flex;align-items:center;gap:6px}
.social-top{position:absolute;right:0;top:8px;display:flex;gap:6px}
.social-top i,.social-foot i{display:block;width:22px;height:22px;border-radius:50%;border:1px solid rgba(255,255,255,.8)}
.brand{position:absolute;left:0;top:48px;display:flex;align-items:center;gap:14px}
.brand-mark{width:64px;height:64px;background:var(--white);border-radius:50%}
.brand-name{font-weight:800;font-size:22px;line-height:1.15;text-transform:uppercase}
.search{position:absolute;right:0;top:58px;width:230px;height:30px;background:var(--white);border-radius:15px;color:#999;font-size:13px;padding:5px 14px}
.main-nav{position:absolute;right:0;top:128px;display:flex;gap:24px;font-weight:700;font-size:15px;text-transform:uppercase}

/* hero */
.hero{height:480px;background:linear-gradient(120deg,#e9f4fc 0%,var(--sky-pale) 45%,#9fd0f2 100%);position:relative}
.hero-arrow{position:absolute;top:218px;width:44px;height:44px;border-radius:50%;background:rgba(40,60,80,.55)}
.hero-arrow.prev{left:28px}.hero-arrow.next{right:28px}
.hero-arrow svg{width:44px;height:44px}

/* welcome */
.welcome{padding-top:40px;height:340px;display:flex;gap:40px}
.welcome-text{width:700px}
.welcome h1{color:var(--blue);font-weight:800;font-size:24px;line-height:1.2;text-transform:uppercase}
.welcome p{margin-top:14px;font-size:13px;line-height:1.7}
.featured{width:320px}
.featured h2,.section-title{font-weight:800;font-size:20px;color:#333;text-transform:uppercase}
.featured h2{border-bottom:2px solid #ddd;padding-bottom:6px}
.video{margin-top:14px;height:150px;background:linear-gradient(135deg,#6a7b8c,#2f3c49);position:relative}
.video svg{position:absolute;left:50%;top:50%;transform:translate(-50%,-50%)}
.featured p{margin-top:10px;font-size:13px}

/* programs */
.programs{background:var(--grey-bg);height:340px;padding-top:30px}
.programs .head{display:flex;justify-content:space-between;align-items:center;border-bottom:2px solid #d4d7da;padding-bottom:8px}
.arrows{display:flex;gap:6px}
.arrows i{display:block;width:22px;height:22px;background:#b7bcc1}
.cards{display:flex;gap:22px;margin-top:18px}
.card{width:252px;background:var(--white);border:1px solid #d9dcdf;height:226px;position:relative}
.card h3{font-size:14px;font-weight:700;color:#333;padding:8px 10px;height:46px;line-height:1.3}
.card .pic{height:80px;margin:0 10px}
.card p{font-size:12px;padding:10px;line-height:1.5}
.card::after{content:"";position:absolute;right:0;bottom:0;border-left:18px solid transparent;border-bottom:18px solid var(--blue)}

/* banner */
.study-banner{height:400px;margin-top:40px;background:linear-gradient(90deg,#8fb7a3 0%,#c7dcc9 40%,#eef4ef 70%,#f6f8f6 100%);position:relative}
.study-copy{position:absolute;left:540px;top:120px;font-family:Oswald,Arial,sans-serif;color:#3a3f44;text-transform:uppercase}
.study-copy .big{font-size:74px;line-height:1;font-weight:500}
.study-copy .sub{font-size:36px;line-height:1.2}
.btn-orange{display:inline-block;background:var(--orange);color:var(--white);font-weight:700;font-family:"Open Sans",Arial,sans-serif}
.study-copy .btn-orange{margin-top:14px;font-size:26px;padding:8px 46px;border-radius:6px}

/* blog + testimonials */
.twin{display:flex;gap:60px;padding-top:46px;height:420px}
.twin>div{width:510px}
.badge{width:52px;height:52px;border-radius:50%;background:var(--blue);display:flex;align-items:center;justify-content:center}
.twin .section-title{margin-top:10px;border-bottom:2px solid #ddd;padding-bottom:6px}
.blog h4{margin-top:14px;color:var(--blue-dark);font-size:15px;font-weight:700}
.meta{font-size:12px;color:#888}
.twin p{font-size:13px;margin-top:10px;line-height:1.6}
.more{display:block;margin-top:18px;color:var(--blue);font-size:13px}
.quote{font-style:italic}
.author{text-align:right;margin-top:16px;font-size:13px;border-top:1px solid #ccc;padding-top:6px;width:200px;margin-left:auto}

/* subscribe */
.subscribe{height:100px;background:var(--grey-bg)}
.subscribe .wrap{display:flex;align-items:center;justify-content:center;gap:18px;height:100px}
.subscribe h2{font-weight:800;font-size:24px;color:#444;text-transform:uppercase}
.subscribe .field{width:300px;height:34px;background:var(--white);border:1px solid #ccc;color:#999;font-size:13px;padding:6px 12px}
.subscribe .btn-orange{height:34px;padding:6px 26px;font-size:13px}

/* footer */
.site-footer{background:var(--footer);color:#d0d4d8;height:644px;padding-top:34px;position:relative}
.cols{display:flex;gap:40px}
.col{width:240px}
.col h5{color:var(--white);font-size:14px;font-weight:700;text-transform:uppercase;margin-bottom:12px}
.col li{list-style:none;font-size:13px;line-height:1.75}
.news li{margin-bottom:8px;line-height:1.4}
.news .date{color:#9aa1a8;font-size:12px;display:block}
.contact li{display:flex;gap:10px;margin-bottom:10px;line-height:1.4}
.contact i{flex:none;width:18px;height:18px;border-radius:50%;background:#5c636b;margin-top:2px}
.partner{position:absolute;left:60px;top:380px;display:flex;align-items:center;gap:16px}
.partner span{color:var(--white);font-weight:700;font-size:14px;text-transform:uppercase;line-height:1.3}
.partner b{display:flex;align-items:center;gap:8px;background:var(--white);color:#222;font-size:16px;padding:10px 14px}
.partner b i{width:16px;height:16px;background:#222}
.social-foot{position:absolute;right:60px;top:500px;display:flex;gap:8px}
.social-foot i{width:28px;height:28px;border-color:#8a9096}
.copyright{position:absolute;left:0;right:0;bottom:0;height:70px;background:var(--footer-dark);font-size:12px;color:#9aa1a8;text-align:right;padding:24px 60px}
</style>
</head>
<body>
<div class="page">
<header class="site-header">
  <div class="wrap">
    <div class="topbar">
      <span>
        <svg width="12" height="12" viewBox="0 0 24 24"><path fill="#fff" d="M6.6 10.8a15 15 0 0 0 6.6 6.6l2.2-2.2c.3-.3.7-.4 1-.2 1.1.4 2.3.6 3.6.6.6 0 1 .4 1 1V20c0 .6-.4 1-1 1A17 17 0 0 1 3 4c0-.6.4-1 1-1h3.5c.6 0 1 .4 1 1 0 1.3.2 2.5.6 3.6.1.3 0 .7-.2 1z"/></svg>
        +260 555 014 270</span>
      <span>
        <svg width="13" height="10" viewBox="0 0 26 20"><rect x="1" y="1" width="24" height="18" fill="none" stroke="#fff" stroke-width="2"/><path d="M1 1l12 10L25 1" fill="none" stroke="#fff" stroke-width="2"/></svg>
        info@corvale-institute.com</span>
    </div>
    <div class="social-top"><i></i><i></i><i></i><i></i><i></i></div>
    <div class="brand">
      <div class="brand-mark"></div>
      <div class="brand-name">Corvale<br>Institute of Business &amp; Technology</div>
    </div>
    <div class="search">Search</div>
    <nav class="main-nav"><a>Home</a><a>About Us</a><a>Courses</a><a>Contact Us</a></nav>
  </div>
</header>

<section class="hero" role="img" aria-label="Professional touching a glowing digital interface with floating charts">
  <span class="hero-arrow prev"><svg viewBox="0 0 44 44"><path d="M25 14l-8 8 8 8" fill="none" stroke="#fff" stroke-width="3"/></svg></span>
  <span class="hero-arrow next"><svg viewBox="0 0 44 44"><path d="M19 14l8 8-8 8" fill="none" stroke="#fff" stroke-width="3"/></svg></span>
</section>

<section class="wrap welcome">
  <div class="welcome-text">
    <h1>Welcome to<br>Corvale Institute of Business and Technology</h1>
    <p>Corvale Institute of Business and Technology (CIBT) is a fast growing Educational &amp; Training Solution Provider, focusing on holistic knowledge and skills enhancement that impact livelihoods. It is established on the core values of making a meaningful and measurable difference on career aspirations and goals through innovative learning and knowledge management interaction. CIBT prepares students not only for professional careers but also inculcates the importance of discipline and equips them physically, mentally, socially and spiritually. The Institution is licensed and registered under the National Vocational Skills Council (NVSC).</p>
  </div>
  <aside class="featured">
    <h2>Featured Video</h2>
    <div class="video" role="img" aria-label="Video still of a student at a laptop">
      <svg width="48" height="48" viewBox="0 0 48 48"><circle cx="24" cy="24" r="23" fill="var(--blue)"/><path d="M19 14l14 10-14 10z" fill="#fff"/></svg>
    </div>
    <p>Lorem ipsum dolor sit amet, consectetur adipiscing elit.</p>
  </aside>
</section>

<section class="programs">
  <div class="wrap">
    <div class="head">
      <h2 class="section-title">Programs Offered</h2>
      <div class="arrows"><i></i><i></i></div>
    </div>
    <div class="cards">
      <article class="card">
        <h3>University Education – Long Distance Learning</h3>
        <div class="pic" role="img" aria-label="Graduates in gowns" style="background:linear-gradient(135deg,#3b4a5c,#8fa2b5)"></div>
        <p>Lorem ipsum dolor sit amet, consectetur adipiscing elit, sed do eiusmod tempor incididunt ut labore et dolore magna aliqua.</p>
      </article>
      <article class="card">
        <h3>Modular Soft Skills</h3>
        <div class="pic" role="img" aria-label="Team meeting around a table" style="background:linear-gradient(135deg,#7a8b9a,#c9d3db)"></div>
        <p>Lorem ipsum dolor sit amet, consectetur adipiscing elit, sed do eiusmod tempor incididunt ut labore et dolore magna aliqua.</p>
      </article>
      <article class="card">
        <h3>Direct to Home (DTH)</h3>
        <div class="pic" role="img" aria-label="Colourful smartphones" style="background:linear-gradient(135deg,#2d8fd5,#e8574a)"></div>
        <p>Lorem ipsum dolor sit amet, consectetur adipiscing elit, sed do eiusmod tempor incididunt ut labore et dolore magna aliqua.</p>
      </article>
      <article class="card">
        <h3>Skillbridge</h3>
        <div class="pic" role="img" aria-label="Business professionals" style="background:linear-gradient(135deg,#5b4a3f,#c8b8a8)"></div>
        <p>Lorem ipsum dolor sit amet, consectetur adipiscing elit, sed do eiusmod tempor incididunt ut labore et dolore magna aliqua.</p>
      </article>
    </div>
  </div>
</section>

<section class="study-banner" role="img" aria-label="Student sitting on grass studying with a laptop">
  <div class="study-copy">
    <div class="big">Online Study</div>
    <div class="sub">Resource which free</div>
    <a class="btn-orange">CLICK HERE</a>
  </div>
</section>

<section class="wrap twin">
  <div class="blog">
    <div class="badge"><svg width="24" height="24" viewBox="0 0 24 24"><path d="M4 20l2-6L16 4l4 4-10 10z" fill="#fff"/></svg></div>
    <h2 class="section-title">From our Blog</h2>
    <h4>Lorem ipsum dolor sit amet, consectetur adipiscing elit</h4>
    <div class="meta">By Admin · 14/08/2015</div>
    <p>Lorem ipsum dolor sit amet, consectetur adipiscing elit, sed do eiusmod tempor incididunt ut labore et dolore magna aliqua. Ut enim ad minim veniam, quis nostrud exercitation ullamco laboris nisi ut aliquip ex ea commodo consequat.</p>
    <a class="more">Read more ›</a>
  </div>
  <div class="testimonials">
    <div class="badge"><svg width="24" height="24" viewBox="0 0 24 24"><path d="M4 18v-6l3-6h3l-2 6h2v6zm10 0v-6l3-6h3l-2 6h2v6z" fill="#fff"/></svg></div>
    <h2 class="section-title">What our people say</h2>
    <p class="quote">"Lorem ipsum dolor sit amet, consectetur adipiscing elit, sed do eiusmod tempor incididunt ut labore et dolore magna aliqua. Ut enim ad minim veniam, quis nostrud exercitation ullamco laboris nisi ut aliquip ex ea commodo consequat."</p>
    <div class="author">Sam Walters</div>
    <a class="more">View our Testimonials ›</a>
  </div>
</section>

<section class="subscribe">
  <div class="wrap">
    <svg width="40" height="30" viewBox="0 0 40 30"><path d="M2 14L38 2 30 28 20 20z" fill="#555"/></svg>
    <h2>Subscribe our Newsletter</h2>
    <div class="field">Enter Your Email</div>
    <a class="btn-orange">SUBSCRIBE</a>
  </div>
</section>

<footer class="site-footer">
  <div class="wrap cols">
    <div class="col">
      <h5>Navigation</h5>
      <ul><li>Home</li><li>About Us</li><li>Courses</li><li>Contact Us</li></ul>
    </div>
    <div class="col">
      <h5>Programs Offered</h5>
      <ul><li>University Education – Long Distance Learning</li><li>Modular Soft Skills</li><li>Direct to Home (DTH)</li><li>Skillbridge</li><li>Skillbridge Skills to Get Career Launched</li><li>Skillbridge Career Growth Program</li><li>Technology Capabilities</li></ul>
    </div>
    <div class="col news">
      <h5>Recent News</h5>
      <ul>
        <li><span class="date">January 14, 2015</span>Lorem ipsum dolor sit amet, consectetur adipiscing elit</li>
        <li><span class="date">January 12, 2015</span>Lorem ipsum dolor sit amet, consectetur adipiscing elit</li>
        <li><span class="date">January 10, 2015</span>Lorem ipsum dolor sit amet, consectetur adipiscing elit</li>
      </ul>
    </div>
    <div class="col contact">
      <h5>Contact Info</h5>
      <ul>
        <li><i></i>18 Harbour Crescent, Elm Park, Riverside, Lusaka</li>
        <li><i></i>Phone:<br>+260 555 014 270</li>
        <li><i></i>Mobile:<br>+260 555 098 412</li>
        <li><i></i>info@corvale-institute.com</li>
      </ul>
    </div>
  </div>
  <div class="partner"><span>In conjunction<br>with Skillbridge</span><b><i></i>SKILLBRIDGE</b></div>
  <div class="social-foot"><i></i><i></i><i></i><i></i><i></i></div>
  <div class="copyright">© 2015 Corvale Institute of Business and Technology. All Rights Reserved.</div>
</footer>
</div>
</body>
</html>
```